BRAND BOOK design

We are a new swimwear brand. We have a vague idea of what we want. We have some colors we would like to use. We would love someone who can provide simple, sophisticated yet an edgy design for our first brand book. The brand book will contain our campaign photos and you will have to come up with layouts and simple designs to insert these photos and short quotes or descriptions. The brand book will contain our brand identity and express the vibes we want our customers to feel get from our brand.

Target Market(s)

US and Australia

Industry/Entity Type

Fashion

Font styles to use
Other font styles liked:
• Futura Medium

Colors
f9d9e8
cfcfcf
ffffff

Requirements
Must have
• simple modern layout with pop elements.
• photos must be placed with enough space.
• also need minimal space for words.
Nice to have
• Simple layouts that aren't common. Designs that can show our identity.
• Please refer to our website (under construction): www.velmorantiquell.com
Should not have
• mere copies of other brand designs

```html
<!DOCTYPE html>
<html lang="en">
<head>
<meta charset="utf-8">
<title>Velmora Brand Book – Spring 2018</title>
<link href="https://fonts.googleapis.com/css2?family=Jost:wght@200;300;400&family=Courier+Prime&display=swap" rel="stylesheet">
<style>
  :root {
    --board: #1b1b1c;
    --paper: #ffffff;
    --ink: #2a2a2a;
    --ink-soft: #6f6f6f;
    --rule: #8a8a8a;
    --label: #3ddc4f;
    --sky-top: #9ebde6;
    --sky-low: #b7cdea;
    --sea: #3f7fae;
    --surf: #c9d9e6;
    --sand-wet: #8eaac8;
    --sand: #e8e1d6;
    --blush: #f9d9e8;
    --mist: #cfcfcf;
  }
  * { box-sizing: border-box; margin: 0; padding: 0; }
  html, body { width: 1200px; height: 1200px; overflow: hidden; background: var(--board); }
  body { position: relative; font-family: "Jost", "Futura", sans-serif; }

  .spread { position: absolute; width: 564px; height: 355px; background: var(--paper); overflow: hidden; }
  .spread--cover { left: 24px; top: 128px; }
  .spread--welcome { left: 612px; top: 128px; }
  .spread--philosophy { left: 24px; top: 716px; }
  .spread--values { left: 612px; top: 716px; }

  .file-label {
    position: absolute; width: 120px; margin-left: -60px; text-align: center;
    font-family: "Courier Prime", monospace; font-size: 10px; color: var(--label);
  }

  .photo { position: absolute; }
  .photo--beach-pose {
    inset: 0;
    background: linear-gradient(180deg, var(--sky-top) 0%, var(--sky-low) 44%, var(--sea) 46%, var(--sea) 52%, var(--surf) 58%, var(--sea) 64%, var(--sand-wet) 80%, #a9bdd3 100%);
  }
  .photo--hat { left: 312px; top: 47px; width: 205px; height: 308px;
    background: linear-gradient(180deg, #dfe9f3 0%, #eef2f5 65%, #5a7fa0 67%, #e9e2d7 72%, #efe8dd 100%); }
  .photo--shoreline { left: 291px; top: 0; width: 236px; height: 355px;
    background: linear-gradient(180deg, #f1f4f7 0%, #e3ecf2 20%, #8fb0c8 26%, #d6e2ea 40%, #e7e0d4 70%, #d9cdbb 100%); }
  .photo--sand-walk { left: 0; top: 0; width: 367px; height: 355px;
    background: linear-gradient(90deg, rgba(255,255,255,0) 55%, rgba(255,255,255,0.75) 100%),
                linear-gradient(180deg, #f4f5f6 0%, #eceef0 28%, #d9d1c4 34%, #cbbfae 100%); }

  .corner { position: absolute; width: 28px; height: 28px; border-top: 1px solid var(--rule); border-left: 1px solid var(--rule); }

  .cover-wordmark {
    position: absolute; left: 36px; top: 16px; width: 44px; height: 318px;
    display: flex; align-items: center; justify-content: center;
  }
  .cover-wordmark span {
    transform: rotate(-90deg); white-space: nowrap;
    font-weight: 200; font-size: 50px; letter-spacing: 6px; color: var(--ink);
  }
  .cover-season {
    position: absolute; right: 16px; top: 20px;
    font-size: 34px; font-weight: 400; letter-spacing: 0.5px; color: var(--paper);
  }

  .welcome-kicker {
    position: absolute; left: 32px; top: 256px;
    font-size: 13px; font-weight: 300; color: var(--ink-soft); letter-spacing: 0.2px;
  }
  .welcome-wordmark {
    position: absolute; left: 34px; top: 272px;
    font-size: 46px; font-weight: 200; color: var(--ink); letter-spacing: 3px; line-height: 1;
  }

  .section-title {
    position: absolute; font-weight: 200; color: var(--ink); line-height: 1; letter-spacing: 0.5px;
  }
  .philosophy-title { left: 36px; top: 44px; font-size: 35px; }
  .philosophy-text {
    position: absolute; left: 37px; top: 134px;
    font-size: 13px; font-weight: 300; color: var(--ink-soft); line-height: 19px; text-transform: uppercase;
  }
  .values-title { left: 403px; top: 36px; font-size: 36px; line-height: 45px; }
  .values-list {
    position: absolute; left: 413px; top: 202px; list-style: none;
    font-size: 15px; font-weight: 300; color: var(--ink-soft); line-height: 23.3px; text-transform: uppercase;
  }
</style>
</head>
<body>

  <section class="spread spread--cover">
    <div class="photo photo--beach-pose" role="img" aria-label="Campaign photo: model in a white one-piece swimsuit posing at the shoreline under a clear blue sky"></div>
    <h1 class="cover-wordmark"><span>VELMORA</span></h1>
    <p class="cover-season">SPRING 2018</p>
  </section>
  <p class="file-label" style="left:309px; top:588px;">01.png</p>

  <section class="spread spread--welcome">
    <span class="corner" style="left:296px; top:34px;"></span>
    <div class="photo photo--hat" role="img" aria-label="Campaign photo: model in a white sun hat, grey tee and white bikini bottom on the beach"></div>
    <p class="welcome-kicker">WELCOME TO THE WORLD OF</p>
    <h2 class="welcome-wordmark">VELMORA</h2>
  </section>
  <p class="file-label" style="left:897px; top:588px;">02.png</p>

  <section class="spread spread--philosophy">
    <h2 class="section-title philosophy-title">PHILOSOPHY</h2>
    <span class="corner" style="left:26px; top:127px;"></span>
    <p class="philosophy-text">Another layer of skin made<br>with love,<br>for the body and mind</p>
    <div class="photo photo--shoreline" role="img" aria-label="Campaign photo: model in a white strappy one-piece and patterned headscarf by the sea"></div>
  </section>
  <p class="file-label" style="left:309px; top:1176px;">03.png</p>

  <section class="spread spread--values">
    <div class="photo photo--sand-walk" role="img" aria-label="Campaign photo: model in white swimwear with a wrap skirt walking on sand, fading to white"></div>
    <h2 class="section-title values-title">BRAND<br>CORE<br>VALUES</h2>
    <span class="corner" style="left:402px; top:194px;"></span>
    <ul class="values-list">
      <li>Individuality</li>
      <li>Comfort</li>
      <li>Quality</li>
      <li>Style</li>
    </ul>
  </section>
  <p class="file-label" style="left:897px; top:1176px;">04.png</p>

</body>
</html>
```